Logo and Website Design for QR.KA Horizon - a Software Engineering and IT company

Software engineering and IT are two different disciplines - and yet inseparably linked. At QR.KA Horizon, we combine both worlds and ensure that our software solutions are not only innovative and powerful, but also integrate perfectly into existing IT landscapes. Vision stands more for imagination, so it is not neccessary something what has to do with visualisation. Please consider that the winning competitor is also instructed to make a logo for the company. So please make a suitable logo for QR.KA Horizon to which the website fits to and show it during the website creation process. A good Logo desing is important for winning the competition. The website should contain a landing page with inspiring, perhaps futuristic photos of a datacenter and lines of code. Eventuelly flewent integrated in the text. On the landing page the company should introduced with a small text (max 250 words) followed by a section with a short text to one of our products nearby a graphic visualising the architecture of the product. The menue should be on top and fixed during scrolling and consist of the menue items home, solutions, who are we and a contact button. There should be a footer for linking social media, rights and Impressum. Only as an idea not a must. The very first view on the landing page could also be the menue bar and below of it a transparent unsharp photo (e.g. datacenter, lines of code, both ;) with the company name in the center.

###############################################################

Hi Designers,

Despite your very good approaches for describing QR.KA Horizon, here a short introduction (german text) from ourself:

------
QR.KA Horizon – Ihr Partner für ganzheitliche Softwarelösungen

Die QR.KA Horizon ist ein dynamisches Unternehmen, das sich nicht nur auf die Konzeption, das Design und die Entwicklung maßgeschneiderter Software spezialisiert hat, sondern auch deren reibungslosen Betrieb sicherstellt. Mit einem Team aus erfahrenen Softwarearchitekten und IT-Professionals verbinden wir modernste Softwareentwicklung mit tiefgehendem IT-Know-how – für Lösungen, die nachhaltig, leistungsstark und zukunftssicher sind.

Software Engineering trifft IT – Perfektion in Kombination
Software Engineering und IT sind zwei unterschiedliche Disziplinen – und doch untrennbar miteinander verbunden. Wir bei QR.KA Horizon vereinen beide Welten und sorgen dafür, dass unsere Softwarelösungen nicht nur innovativ und leistungsfähig sind, sondern sich auch perfekt in bestehende IT-Landschaften integrieren.

Expertise mit Fokus auf Healthcare & komplexe IT-Umgebungen
Unsere Experten bringen jahrzehntelange Erfahrung aus dem Healthcare-Sektor mit und unterstützen IT-Abteilungen großer Kliniken in der Entwicklung und Optimierung von Softwarelösungen. Von Anwendungssoftware bis hin zu Steuerungssystemen – unsere Softwareingenieure wissen genau, worauf es ankommt.

Ganzheitlicher Ansatz – über die Software hinaus
Wir entwickeln nicht nur Software, sondern übernehmen auch die Verantwortung für deren stabile und effiziente Betriebsumgebung. Egal, ob on-premises, in der Cloud oder als SaaS-Lösung – wir kümmern uns um den kompletten Lifecycle Ihrer Anwendung.

Ihre Vision – unsere Mission.
Ob Neuentwicklung einer SaaS-Anwendung oder die Migration bestehender Lösungen in eine moderne SaaS-Umgebung – mit QR.KA Horizon haben Sie einen starken Partner an Ihrer Seite.

Lassen Sie uns gemeinsam die Zukunft Ihrer Software gestalten!
--------------

Our first solution called "Clear Record Transfer Gateway" (CLURA)
-------------------
Teilen Sie Ihre Daten sicher – ohne Kompromisse!

Sie nutzen eine relationale Datenbank (Brightcask, Tabulon Hub, Vellumdb etc.) und möchten ausgewählte Daten mit Dritten teilen – sei es für ein Data Warehouse, Business Controller, Lieferanten oder Kunden? Doch dabei sollen Datensicherheit, Integrität und Verfügbarkeit Ihrer primären Lösung in keiner Weise gefährdet werden?

Mit unserer Lösung erhalten Sie genau das: Maximalen Schutz für Ihre Anwendung bei gleichzeitigem Nutzen durch autorisierte Dritte – ganz ohne teure Lizenzkosten für eine Schattendatenbank.

Lassen Sie uns gemeinsam herausfinden, wie Sie Ihre Daten sicher und effizient nutzen können. Kontaktieren Sie uns – wir zeigen Ihnen, was möglich ist!
---------------------

Our second solution MIVO:
---------------------
MIVO – Program for a Tone Matching Instrument ist die smarte Lösung für Unternehmen, die bei Farbgenauigkeit keine Kompromisse machen. Die Software erkennt Farbabweichungen zwischen Mustern vollautomatisch, beschreibt sie verständlich und sorgt so für gleichbleibend hohe Produktqualität – schnell, visuell und präzise. Perfekt für alle, die Farbe zur Vertrauenssache machen.
-------------------------

Thanks,
Gerold

Target Market(s)

IT Professionals from any sector

Industry/Entity Type

Healthcare and other

Coding

Coded - Design and coding required

Number of Pages Required

1 page

Font styles to use
Sans Serif

Colors
0054AA
0677BA
7BADD7
CADEEF
E8F1F8
0094D4
00A9DD
6FCCEA
C7EBF8
E9F6FB
00AB8E
00BBA5
67D7C9
C6EFE9
E9F9F6

Requirements
Must have
• Please see description
Nice to have
• On the landing page the company should introduced with a small text (max 250 words) followed by a section with a short text to one of our products nearby a graphic visualising the architecture of the product. The menue should be on top and fixed during scrolling and consist of the menue items home, solutions, who are we and a contact button. There should be a footer for linking social media, rights and Impressum. Only as an idea not a must. The very first view on the landing page could also be the menue bar and below of it a transparent unsharp photo (e.g. datacenter, lines of code, both ;) with the company name in the center.
Should not have
• Please see description

```html
<!DOCTYPE html>
<html lang="de">
<head>
<meta charset="utf-8">
<title>QR.KA Horizon – Software Engineering &amp; IT</title>
<link rel="stylesheet" href="https://fonts.googleapis.com/css2?family=Poppins:wght@400;500;600;700&family=Source+Sans+3:wght@400;600;700&display=swap">
<style>
:root{
  --blue:#0054AA;
  --blue-mid:#0677BA;
  --sky:#7BADD7;
  --sky-pale:#CADEEF;
  --ice:#E8F1F8;
  --cyan:#00A9DD;
  --cyan-pale:#C7EBF8;
  --green:#00AB8E;
  --ink:#111111;
  --navy:#0b1a52;
  --navy-deep:#0a1646;
  --white:#ffffff;
}
*{box-sizing:border-box;margin:0;padding:0}
html,body{width:1200px;height:3397px;overflow:hidden}
body{position:relative;background:var(--white);font-family:"Source Sans 3",Arial,sans-serif;color:var(--ink)}
.abs{position:absolute}
.art{position:absolute;display:block}

/* nav */
.site-nav{position:absolute;left:141px;top:36px;width:918px;height:55px;background:var(--white);border-radius:28px;box-shadow:0 4px 18px rgba(0,40,100,.12);z-index:5}
.brand{position:absolute;left:37px;top:13px;font-family:Poppins,sans-serif;font-weight:700;font-size:24px;letter-spacing:-.3px;color:var(--blue);line-height:28px}
.menu{position:absolute;right:55px;top:18px;display:flex;gap:40px;font-family:Poppins,sans-serif;font-size:13px;color:#222}
.menu .drop::after{content:"";display:inline-block;margin-left:6px;border:3.5px solid transparent;border-top:4px solid #444;vertical-align:middle}

/* hero */
.hero-title{left:152px;top:182px;font-family:Poppins,sans-serif;font-weight:700;font-size:48px;line-height:57px;color:var(--ink)}
.hero-sub{left:152px;top:374px;font-family:Poppins,sans-serif;font-size:16px;line-height:30px;color:#111}
.btn-solid{position:absolute;background:var(--blue);color:var(--white);border-radius:20px;font-size:14px;display:flex;align-items:center;justify-content:center}
.btn-ghost{position:absolute;border:1.5px solid var(--green);border-radius:20px;font-size:14px;display:flex;align-items:center;justify-content:center;color:#111;background:var(--white)}

/* about */
.about-head{left:649px;top:848px;width:430px;font-weight:700;font-size:28px;line-height:35px;color:var(--ink)}
.c-blue{color:var(--blue)}
.c-green{color:var(--green)}
.about-text{left:649px;top:932px;width:412px;font-size:13.5px;line-height:24px;color:#222}

/* product */
.section-title{left:0;width:1200px;top:1327px;text-align:center;font-weight:700;font-size:28px;color:var(--blue)}
.section-lead{left:320px;width:560px;top:1379px;text-align:center;font-size:13.5px;line-height:21px;color:#222}
.prod-head{font-size:18px;line-height:28px;color:#111;font-weight:600}
.prod-head span{font-weight:400}
.prod-text{font-size:13px;line-height:23px;color:#222}

/* cta */
.cta-head{left:142px;top:2713px;width:470px;font-weight:700;font-size:25px;line-height:32px;color:var(--blue)}

/* footer */
.site-footer{position:absolute;left:0;top:3037px;width:1200px;height:360px;background:var(--navy)}
.foot-bottom{position:absolute;left:0;top:312px;width:1200px;height:48px;background:var(--navy-deep);font-family:Poppins,sans-serif;font-size:12px;color:#c9d3ee}
.foot-col-title{position:absolute;font-family:Poppins,sans-serif;font-weight:600;font-size:16px;color:var(--white)}
.foot-col-title::after{content:"";position:absolute;left:0;top:28px;width:26px;height:2px;background:var(--green)}
.foot-text{position:absolute;font-family:Poppins,sans-serif;font-size:13px;color:#e3e8f6;line-height:28px}
.foot-list{list-style:none}
.foot-list li{position:relative;padding-left:16px;height:28px}
.foot-list li::before{content:"";position:absolute;left:0;top:10px;border:4px solid transparent;border-left:6px solid var(--cyan)}
.social{position:absolute;top:3258px;width:18px;height:18px;border-radius:50%;border:2px solid var(--white)}
.contact-icon{position:absolute;width:30px;height:30px;border-radius:50%;background:#25357a}
.news-input{position:absolute;left:860px;top:3182px;width:198px;height:37px;border:1px solid #5b6aa6;border-radius:20px;font-family:Poppins,sans-serif;font-size:11px;color:#aab4d8;padding:11px 20px}
</style>
</head>
<body>

<!-- hero image -->
<svg class="art" style="left:505px;top:0" width="695" height="670" viewBox="0 0 695 670" role="img" aria-label="Foto eines Rechenzentrums mit leuchtenden Codezeilen">
  <defs>
    <linearGradient id="heroGrad" x1="0" y1="0" x2="1" y2="1">
      <stop offset="0" stop-color="#1a2a3d"/>
      <stop offset=".35" stop-color="#5a3a1e"/>
      <stop offset=".6" stop-color="#0e3a5c"/>
      <stop offset="1" stop-color="#0b2238"/>
    </linearGradient>
  </defs>
  <path d="M60 0 C30 90 0 180 20 300 C40 440 90 540 200 530 C330 515 400 440 520 470 C600 490 650 560 695 660 L695 0 Z" fill="#cde9f8"/>
  <path d="M70 0 C40 90 15 180 30 295 C50 420 100 510 200 500 C320 488 390 420 510 445 C590 460 650 510 695 560 L695 0 Z" fill="url(#heroGrad)"/>
</svg>

<nav class="site-nav">
  <div class="brand">QR.KA HORIZON</div>
  <div class="menu">
    <span>Heim</span><span class="drop">Lösungen</span><span class="drop">Wer Sind Wir</span>
  </div>
</nav>

<h1 class="abs hero-title">Mit Präzision<br>Die Zukunft<br>Voramtreiben</h1>
<p class="abs hero-sub">Innovative Lösungen für Leistung,<br>Sicherheit und Skalierbarkeit</p>
<div class="btn-solid" style="left:150px;top:451px;width:156px;height:34px">Legen Sie los</div>

<!-- about -->
<svg class="art" style="left:0;top:700px" width="600" height="570" viewBox="0 0 600 570" role="img" aria-label="Illustration: Laptop mit Zahnrad, Pfeilen und Programmfenstern">
  <defs>
    <linearGradient id="aboutGrad" x1="0" y1="0" x2="1" y2="1">
      <stop offset="0" stop-color="#bfe2f8"/><stop offset="1" stop-color="#4a8fd0"/>
    </linearGradient>
  </defs>
  <path d="M0 90 C60 40 140 10 240 5 C300 0 320 40 322 100 C420 110 590 180 595 320 C600 470 440 565 300 566 C170 568 70 510 0 470 Z" fill="var(--ice)"/>
  <rect x="150" y="110" width="410" height="360" rx="40" fill="url(#aboutGrad)" opacity=".85"/>
</svg>
<h2 class="abs about-head"><span class="c-blue">QR.KA</span> <span class="c-green">Horizon</span>-Ihr Partner für ganzheitliche Softwarelösungen</h2>
<p class="abs about-text">QR.KA Horizon ist ein dynamisches Unternehmen, das sich nicht nur auf die Konzeption, Gestaltung und Entwicklung von Individualsoftware spezialisiert hat, sondern auch für deren reibungslosen Betrieb sorgt. Mit einem Team aus erfahrenen Softwarearchitekten und IT-Profis verbinden wir modernste Softwareentwicklung mit fundiertem IT-Know-how - für Lösungen, die nachhaltig, leistungsstark und zukunftssicher sind.</p>

<!-- featured product -->
<h2 class="abs section-title">Ausgewähltes <span class="c-green">Produkt</span></h2>
<p class="abs section-lead">Lorem ipsum dolor sit amet, consectetuer adipiscing elit, sed diam nonummy nibh euismod tincidunt ut laoreet dolore magna aliquam erat volutpat wisi enim ad minim veniam</p>

<h3 class="abs prod-head" style="left:142px;top:1505px">Offene Datenaustauschschnittstelle <span class="c-green">(CLURA)</span></h3>
<p class="abs prod-text" style="left:142px;top:1544px;width:420px">Sie verwenden eine relationale Datenbank (Brightcask, Tabulon Hub, Vellumdb usw.) und möchten ausgewählte Daten mit Dritten teilen - sei es für ein Data Warehouse, Business Controller, Lieferanten oder Kunden? Sie wollen aber die Datensicherheit, -integrität und -verfügbarkeit Ihrer primären Lösung in keiner Weise gefährden? Mit unserer Lösung erhalten Sie genau das: maximalen Schutz für Ihre Anwendung bei gleichzeitiger Nutzung durch autorisierte Dritte - ohne die teuren Lizenzkosten für eine Schattendatenbank.<br>Lassen Sie uns gemeinsam herausfinden, wie Sie Ihre Daten sicher und effizient nutzen können.</p>
<div class="btn-ghost" style="left:141px;top:1799px;width:155px;height:36px">Kontaktieren Sie uns</div>

<svg class="art" style="left:630px;top:1385px" width="570" height="570" viewBox="0 0 570 570" role="img" aria-label="Architekturgrafik: vernetzte Laptops um einen zentralen Datenknoten">
  <defs>
    <linearGradient id="odGrad" x1="0" y1="0" x2="1" y2="1">
      <stop offset="0" stop-color="#2a4fb0"/><stop offset="1" stop-color="#0d2f8a"/>
    </linearGradient>
    <linearGradient id="odArt" x1="0" y1="0" x2="1" y2="1">
      <stop offset="0" stop-color="#8a7be0"/><stop offset=".5" stop-color="#3dd6cf"/><stop offset="1" stop-color="#5a48c4"/>
    </linearGradient>
  </defs>
  <path d="M570 0 C540 90 480 100 420 95 C320 85 250 90 200 150 C150 210 130 300 100 380 C70 460 150 520 260 505 C380 490 460 500 570 520 Z" fill="url(#odGrad)"/>
  <rect x="25" y="130" width="390" height="330" rx="30" fill="url(#odArt)" opacity=".8"/>
  <g fill="var(--green)">
    <circle cx="300" cy="530" r="2"/><circle cx="320" cy="530" r="2"/><circle cx="340" cy="530" r="2"/><circle cx="360" cy="530" r="2"/><circle cx="380" cy="530" r="2"/><circle cx="400" cy="530" r="2"/><circle cx="420" cy="530" r="2"/><circle cx="440" cy="530" r="2"/>
    <circle cx="340" cy="548" r="2"/><circle cx="360" cy="548" r="2"/><circle cx="380" cy="548" r="2"/><circle cx="400" cy="548" r="2"/><circle cx="420" cy="548" r="2"/><circle cx="440" cy="548" r="2"/><circle cx="460" cy="548" r="2"/><circle cx="480" cy="548" r="2"/>
  </g>
</svg>

<!-- second product -->
<svg class="art" style="left:0;top:1905px" width="1200" height="670" viewBox="0 0 1200 670" role="img" aria-label="Hintergrund mit Binärcode und Illustration einer Lupe über einem Laptop">
  <defs>
    <linearGradient id="sqBand" x1="0" y1="0" x2="0" y2="1">
      <stop offset="0" stop-color="#f4f8fc"/><stop offset="1" stop-color="#e6eef8"/>
    </linearGradient>
    <linearGradient id="sqBlob" x1="0" y1="0" x2="1" y2="1">
      <stop offset="0" stop-color="#0c3c9c"/><stop offset="1" stop-color="#1c4fb8"/>
    </linearGradient>
    <linearGradient id="sqArt" x1="0" y1="0" x2="1" y2="1">
      <stop offset="0" stop-color="#6b4fd6"/><stop offset=".6" stop-color="#3a2aa8"/><stop offset="1" stop-color="#8ab8f0"/>
    </linearGradient>
  </defs>
  <path d="M0 0 L1200 35 L1200 560 C900 600 600 640 0 540 Z" fill="url(#sqBand)"/>
  <path d="M0 0 C150 10 330 40 430 90 C470 180 440 330 350 430 C240 520 100 500 0 560 Z" fill="url(#sqBlob)"/>
  <rect x="150" y="60" width="430" height="400" rx="40" fill="url(#sqArt)" opacity=".85"/>
</svg>
<h3 class="abs prod-head" style="left:653px;top:2055px;width:380px">Software zur Qualitätssicherung der Farbgenauigkeit <span class="c-green">( MIVO)</span></h3>
<p class="abs prod-text" style="left:652px;top:2121px;width:410px">MIVO ist die intelligente Lösung für Unternehmen, die bei der Farbgenauigkeit keine Kompromisse eingehen. Die Software erkennt automatisch Farbabweichungen zwischen Mustern, beschreibt sie eindeutig und sorgt so für eine gleichbleibend hohe Produktqualität - schnell, visuell und präzise. Perfekt für alle, die Farbe zur Vertrauenssache machen.</p>
<div class="btn-ghost" style="left:650px;top:2283px;width:155px;height:36px">Kontaktieren Sie uns</div>

<!-- call to action -->
<h2 class="abs cta-head">Ermutigung der Besucher, sich mit Ihnen in Verbindung zu setzen, um Lösungen <span class="c-green">für die sichere und effiziente Nutzung ihrer Daten zu finden.</span></h2>
<div class="btn-ghost" style="left:141px;top:2858px;width:155px;height:36px">Kontaktieren Sie uns</div>
<svg class="art" style="left:560px;top:2650px" width="615" height="375" viewBox="0 0 615 375" role="img" aria-label="Illustration: Computer mit Tastatur, Maus, Zahnrädern und Werkzeug">
  <defs>
    <linearGradient id="ctaGrad" x1="0" y1="0" x2="1" y2="1">
      <stop offset="0" stop-color="#1f8fdc"/><stop offset=".6" stop-color="#0a4a9a"/><stop offset="1" stop-color="#53b6ee"/>
    </linearGradient>
  </defs>
  <path d="M30 260 C100 200 220 60 360 50 C480 40 600 120 600 230 C600 320 470 370 330 370 C190 370 0 320 30 260 Z" fill="url(#ctaGrad)" opacity=".85"/>
</svg>

<!-- footer -->
<footer class="site-footer">
  <div class="abs" style="left:137px;top:98px;width:28px;height:28px;border-radius:50%;border:2px solid var(--white)"></div>
  <div class="abs" style="left:177px;top:97px;font-family:Poppins,sans-serif;font-weight:600;font-size:21px;color:var(--white)">QR.KA HORIZON</div>
  <p class="foot-text" style="left:140px;top:145px;width:220px;line-height:23px">Innovative Software trifft auf echte IT-Expertise</p>

  <div class="foot-col-title" style="left:435px;top:92px">Quicklinks</div>
  <ul class="foot-text foot-list" style="left:435px;top:140px">
    <li>Heim</li><li>Lösungen</li><li>Wer Sind Wir</li><li>Kontakt</li>
  </ul>

  <div class="foot-col-title" style="left:616px;top:92px">Kontakt Uns</div>
  <div class="contact-icon" style="left:616px;top:138px">
    <svg width="30" height="30" viewBox="0 0 30 30" aria-hidden="true"><path d="M11 9 C10 9 9 10 9 11 C9 16 14 21 19 21 C20 21 21 20 21 19 L21 17.5 L18 16.5 L17 17.8 C15 17 13 15 12.2 13 L13.5 12 L12.5 9 Z" fill="var(--white)"/></svg>
  </div>
  <div class="foot-text" style="left:661px;top:138px">(123)-555-0142</div>
  <div class="contact-icon" style="left:616px;top:182px">
    <svg width="30" height="30" viewBox="0 0 30 30" aria-hidden="true"><rect x="9" y="10.5" width="12" height="9" rx="1" fill="none" stroke="var(--white)" stroke-width="1.4"/><path d="M9 11 L15 16 L21 11" fill="none" stroke="var(--white)" stroke-width="1.4"/></svg>
  </div>
  <div class="foot-text" style="left:661px;top:182px">info@qrka-horizon.example</div>

  <div class="foot-col-title" style="left:860px;top:90px">Newsletter Abonnieren</div>
  <div class="btn-solid" style="left:860px;top:203px;width:198px;height:37px;background:var(--blue-mid);font-family:Poppins,sans-serif;font-weight:600;font-size:13px">Jetzt Abonnieren</div>

  <div class="foot-bottom">
    <span class="abs" style="left:140px;top:15px">Copyright © 2025 Qarka Horizon Software Engineering Technology | Alle Rechte Vorbehalten.</span>
    <span class="abs" style="left:990px;top:15px">Impressum</span>
  </div>
</footer>
<div class="news-input">Eingeben E-Mail</div>
<div class="social" style="left:137px" role="img" aria-label="Soziales Netzwerk 1"></div>
<div class="social" style="left:177px" role="img" aria-label="Soziales Netzwerk 2"></div>
<div class="social" style="left:222px" role="img" aria-label="Soziales Netzwerk 3"></div>
<div class="social" style="left:268px" role="img" aria-label="Soziales Netzwerk 4"></div>

</body>
</html>
```